Website Development for vaultmerrow.com.au

Build a new Wordpress/Responsive website for vaultmerrow.com.au

Target Market(s)

Compliance Managers, Risk Managers, Information Security and Cyber Security Professionals, Chief Data/Digital Officers, Chief Operating/Financial Officers, Business Continuity Professionals, Disaster Recovery Planners, Small Business Owners, Local/Federal Government entities

Industry/Entity Type

Data Service

Coding

Coded - Design and coding required

Number of Pages Required

5+ page

Font styles to use
Sans Serif

Colors

Designer to choose colors to be used in the design.

Requirements
Must have
• 1. Site Structure: Home Page plus the following chapter-pages for a) Services b) About c) Resources d) Blog e) Contact Us
• 2. Prefer site to built on wordpress and we can purchase a theme if needed (we currently use Kelp9 for other sites)
• 3. Blog needs to be wordpress based
• 4. We will host the site ourselves on our own servers
• 5. Responsive Design
Nice to have
• 1. Livechat capability/interface
• 2. Capability for marketing automation integration (such as hubspot, marketo, infusionsoft etc)
• 3. Capability for CRM integration (Salesforce)

```html
<!DOCTYPE html>
<html lang="en">
<head>
<meta charset="utf-8">
<title>Vaultmerrow — Data Security Services</title>
<link href="https://fonts.googleapis.com/css2?family=Mulish:wght@400;600;700;800&family=Roboto:wght@400;500;700&display=swap" rel="stylesheet">
<style>
:root{
  --blue:#1565c0;
  --blue-dark:#0c3f8f;
  --navy:#0a2a78;
  --sky:#e8f1fb;
  --ink:#222;
  --muted:#555;
  --line:#cfd8e3;
  --black:#0b0b0b;
  --white:#fff;
}
*{box-sizing:border-box;margin:0;padding:0}
html,body{width:1200px;height:4306px;overflow:hidden}
body{position:relative;font-family:"Mulish",Arial,sans-serif;color:var(--ink);background:var(--white)}
.abs{position:absolute}
h1,h2,h3{font-family:"Roboto",Arial,sans-serif}

/* top bar */
.topbar{left:0;top:0;width:1200px;height:57px;background:var(--blue-dark);color:var(--white);font-size:14px}
.topbar .contact{left:143px;top:19px;display:flex;gap:32px}
.topbar .contact span{display:flex;align-items:center;gap:8px}
.topbar .follow{right:143px;top:17px;display:flex;align-items:center;gap:8px;font-weight:700}
.social{display:inline-block;width:20px;height:20px;border-radius:3px}
.s1{background:#e04b3a}.s2{background:#2aa3ef}.s3{background:#1e6fbf}.s4{background:#d62d2d}

/* nav */
.nav{left:0;top:57px;width:1200px;height:81px;background:var(--white);box-shadow:0 2px 6px rgba(0,0,0,.08)}
.brand{display:flex;align-items:center;gap:10px;font-family:"Mulish",sans-serif;font-weight:800;font-size:30px;color:var(--blue)}
.brand .dot{width:26px;height:26px;border-radius:50%;background:var(--blue)}
.nav .brand{left:143px;top:20px}
.menu{display:flex;gap:38px;font-size:14px;font-weight:600;color:#333;text-transform:uppercase}
.nav .menu{left:531px;top:32px}
.menu .active{color:var(--blue);position:relative}
.menu .active::after{content:"";position:absolute;left:-10px;right:-10px;bottom:-30px;height:3px;background:var(--blue)}

/* hero */
.hero{left:0;top:138px;width:1200px;height:465px;background:linear-gradient(100deg,#0a1f6e 0%,#0f3aa8 55%,#3c8be8 78%,#0d2e8c 100%)}
.hero-title{left:143px;top:145px;font-size:42px;line-height:52px;font-weight:700;color:var(--white)}
.btn-outline{left:143px;top:262px;width:164px;height:48px;border:2px solid var(--white);color:var(--white);font-size:15px;font-weight:700;display:flex;align-items:center;justify-content:center}
.dots{left:566px;top:430px;display:flex;gap:8px}
.dots i{display:block;width:18px;height:4px;background:rgba(255,255,255,.5)}
.dots i.on{background:var(--white)}

/* about */
.about-photo{left:143px;top:683px;width:446px;height:451px;background:linear-gradient(135deg,#e7edf3,#9aa8b8 60%,#2c3646)}
.about-head{left:632px;top:735px;display:flex;align-items:center;gap:14px;font-size:30px;font-weight:700;color:#333}
.about-head .brand{font-size:30px}
.about-text{left:632px;top:808px;width:430px;font-size:13px;line-height:19px;color:var(--muted)}
.about-text p{margin-bottom:8px}
.about-text b{color:var(--blue)}
.about-text .cta{font-size:15px;line-height:22px;color:#222;font-weight:700}
.about-text .cta a{color:var(--blue);font-weight:600;text-decoration:none}

/* services */
.services{left:0;top:1220px;width:1200px;height:566px;background:var(--sky);overflow:hidden}
.sec-title{width:1200px;text-align:center;font-size:36px;font-weight:700;color:#111;left:0}
.sec-text{width:1200px;left:0;text-align:center;font-size:13px;line-height:22px;color:var(--muted)}
.sec-text b{color:var(--blue);font-weight:600}
.halo{left:340px;top:340px;width:520px;height:520px;border-radius:50%;background:rgba(255,255,255,.75)}
.core{left:430px;top:416px;width:345px;height:345px;border-radius:50%;background:var(--blue);display:flex;justify-content:center;padding-top:70px}
.core .brand{color:var(--white);font-size:40px;height:50px}
.core .brand .dot{background:var(--white)}
.svc-icon{width:104px;height:104px;border-radius:50%;background:var(--white);border:5px solid #666;display:flex;align-items:center;justify-content:center}
.svc-icon.blue{border-color:var(--blue)}
.svc-label{font-size:16px;font-weight:700;line-height:20px;color:#333}
.svc-label.blue{color:var(--blue)}

/* whom */
.whom-circle{width:144px;height:144px;border-radius:50%;background:var(--white);box-shadow:0 0 12px rgba(0,0,0,.12);display:flex;align-items:center;justify-content:center}
.whom-circle.active{border:6px solid var(--blue)}
.whom-label{width:200px;text-align:center;font-size:16px;line-height:20px;color:#333}
.whom-label.active{color:var(--blue);font-weight:600}
.arrow-btn{width:36px;height:36px;border-radius:50%;background:var(--white);box-shadow:0 0 8px rgba(0,0,0,.18);display:flex;align-items:center;justify-content:center}

/* team */
.team-bg{left:0;top:2297px;width:1200px;height:720px}
.team-title{color:var(--white)}
.team-sub{left:0;width:1200px;text-align:center;font-size:20px;color:#dfe9f7}
.card{width:190px;height:377px;background:var(--white);border-bottom:6px solid var(--blue-dark)}
.card .photo{position:absolute;left:25px;top:38px;width:140px;height:200px;background:linear-gradient(160deg,#dfe4ea,#8d97a4 70%,#4c5563)}
.card .name{position:absolute;left:0;top:262px;width:190px;text-align:center;font-size:16px;color:#222;text-transform:uppercase}
.card .role{position:absolute;left:0;top:284px;width:190px;text-align:center;font-size:13px;color:#777}
.card .rule{position:absolute;left:30px;top:305px;width:130px;height:1px;background:var(--line)}
.card .soc{position:absolute;left:0;top:315px;width:190px;display:flex;justify-content:center;gap:8px}
.card .soc i{width:9px;height:9px;background:#555;border-radius:2px;display:block}
.card.feature .name{color:var(--blue)}

/* blog */
.blog-card{width:442px;height:268px;background:var(--white);box-shadow:0 4px 14px rgba(0,0,0,.1);border-bottom:6px solid var(--blue)}
.date{width:126px;height:126px;border-radius:50%;background:var(--white);border:8px solid #777;display:flex;flex-direction:column;align-items:center;justify-content:center;color:var(--blue)}
.date b{font-size:42px;line-height:44px;font-family:"Roboto",sans-serif;font-weight:500}
.date span{font-size:13px}
.blog-card h3{position:absolute;top:90px;left:0;width:442px;text-align:center;font-size:17px;color:#111}
.blog-card p{position:absolute;top:124px;left:56px;width:330px;text-align:center;font-size:12.5px;line-height:18px;color:#666}
.blog-card a{position:absolute;top:216px;left:0;width:442px;text-align:center;font-size:14px;color:var(--blue);text-decoration:underline}
.btn-view{left:525px;top:3537px;width:150px;height:38px;border:2px solid var(--blue);color:var(--blue);font-size:14px;display:flex;align-items:center;justify-content:center}

/* get started */
.start{left:0;top:3660px;width:1200px;height:474px;background:linear-gradient(120deg,#1b63c0,#0f4fa8 50%,#1d6ccb)}
.start-title{color:var(--white)}
.form{left:310px;top:3850px;width:646px;height:140px;border:1px solid rgba(255,255,255,.4)}
.field{position:absolute;left:0;width:323px;height:46px;border-bottom:1px solid rgba(255,255,255,.4);color:rgba(255,255,255,.8);font-size:13px;padding:14px 18px}
.field.first{color:var(--white)}
.message{position:absolute;left:323px;top:0;width:323px;height:140px;border-left:1px solid rgba(255,255,255,.4);color:rgba(255,255,255,.8);font-size:13px;padding:14px 18px}
.btn-submit{left:528px;top:4024px;width:146px;height:38px;background:var(--black);color:var(--white);font-size:15px;font-weight:700;display:flex;align-items:center;justify-content:center}
.chat{left:1010px;top:4096px;width:58px;height:58px;border-radius:50%;background:var(--white);box-shadow:0 2px 8px rgba(0,0,0,.3);display:flex;align-items:center;justify-content:center}

/* footer */
.footer{left:0;top:4134px;width:1200px;height:172px;background:var(--black);color:var(--white)}
.footer .brand{left:143px;top:48px;color:var(--white);font-size:32px}
.footer .brand .dot{background:var(--white)}
.footer .menu{left:535px;top:70px;color:var(--white);font-size:13px;font-weight:400;gap:44px}
.footer .rule{left:143px;top:130px;width:914px;height:1px;background:#333}
.footer .copy{left:143px;top:146px;font-size:11px;color:#ccc}
.footer .legal{right:143px;top:146px;font-size:11px;color:#ccc}
</style>
</head>
<body>

<!-- Top bar -->
<div class="abs topbar">
  <div class="abs contact">
    <span><svg width="14" height="14" viewBox="0 0 24 24" fill="#fff"><path d="M6.6 10.8a15 15 0 0 0 6.6 6.6l2.2-2.2a1 1 0 0 1 1-.25 11.4 11.4 0 0 0 3.6.57 1 1 0 0 1 1 1V20a1 1 0 0 1-1 1A17 17 0 0 1 3 4a1 1 0 0 1 1-1h3.5a1 1 0 0 1 1 1c0 1.25.2 2.45.57 3.6a1 1 0 0 1-.25 1z"/></svg>+012-345-678</span>
    <span><svg width="15" height="12" viewBox="0 0 24 18" fill="none" stroke="#fff" stroke-width="2"><rect x="1" y="1" width="22" height="16" rx="2"/><path d="M1 2l11 8 11-8"/></svg>info@vaultmerrow.com</span>
  </div>
  <div class="abs follow">Follow Us on <i class="social s1"></i><i class="social s2"></i><i class="social s3"></i><i class="social s4"></i></div>
</div>

<!-- Navigation -->
<header class="abs nav">
  <div class="abs brand"><span class="dot"></span>Vaultmerrow</div>
  <nav class="abs menu"><span class="active">Home</span><span>About</span><span>Services</span><span>Resources</span><span>Blog</span><span>Contact Us</span></nav>
</header>

<!-- Hero -->
<section class="abs hero" role="img" aria-label="Digital globe with connected network user icons on a deep blue background"></section>
<h1 class="abs hero-title" style="top:283px">Because We Care,<br>We're Security Aware</h1>
<div class="abs btn-outline" style="top:400px">Contact Us Today</div>
<div class="abs dots" style="top:568px"><i></i><i class="on"></i><i></i></div>

<!-- About -->
<div class="abs about-photo" role="img" aria-label="Smiling businessman in a suit working on a laptop"></div>
<div class="abs about-head">About <span class="brand"><span class="dot"></span>Vaultmerrow</span></div>
<div class="abs about-text">
  <p><b>Vaultmerrow</b> It is a long established fact that a reader will be distracted by the readable content of a page when looking at its layout. The point of using Lorem Ipsum is that it has a more-or-less normal distribution.</p>
  <p>The point of using Lorem Ipsum is that it has a more-or-less normal distribution of letters, as opposed to using 'Content here, content here', making it look like readable English.</p>
  <p>Lorem Ipsum is that it has a more-or-less normal distribution of letters, as opposed to using 'Content here, content here', making it look like readable English has a more-or-less normal.</p>
  <p>The point of using Lorem Ipsum is that it has a more-or-less normal distribution of letters, as opposed to using 'Content here, content here', making it look like readable English.</p>
  <p class="cta">Get the support you need now. <a>Contact our 24/7 support line to get started.</a></p>
</div>

<!-- Services -->
<section class="abs services">
  <h2 class="abs sec-title" style="top:50px">SERVICES</h2>
  <div class="abs sec-text" style="top:118px">
    <b>Vaultmerrow</b> It is a long established fact that a reader will be distracted by the readable content of a page when looking at its layout.<br>
    The point of using Lorem Ipsum is that it has a more-or-less normal distribution of letters.<br>
    <span style="display:block;height:8px"></span>
    The point of using Lorem Ipsum is that it has a more-or-less <b>Vaultmerrow</b> normal distribution of letters, as opposed to using<br>
    'Content here, content here', making it look like readable English
  </div>
  <div class="abs halo"></div>
  <div class="abs core"><div class="brand"><span class="dot"></span>Vaultmerrow</div></div>

  <div class="abs svc-icon blue" style="left:450px;top:235px"><svg width="44" height="44" viewBox="0 0 24 24" fill="none" stroke="#1565c0" stroke-width="1.5"><path d="M7 18a4 4 0 0 1 0-8 5 5 0 0 1 9.6-1.5A4 4 0 0 1 17 18z"/><rect x="9" y="12" width="6" height="4"/></svg></div>
  <div class="abs svc-label blue" style="left:255px;top:262px;text-align:right;width:175px">Data Management<br>Platforms</div>

  <div class="abs svc-icon" style="left:637px;top:235px"><svg width="44" height="44" viewBox="0 0 24 24" fill="none" stroke="#444" stroke-width="1.5"><circle cx="12" cy="12" r="3"/><path d="M12 2v3M12 19v3M2 12h3M19 12h3M4.9 4.9l2.1 2.1M17 17l2.1 2.1M4.9 19.1L7 17M17 7l2.1-2.1"/></svg></div>
  <div class="abs svc-label" style="left:770px;top:274px">Industry Solutions</div>

  <div class="abs svc-icon" style="left:313px;top:370px"><svg width="42" height="42" viewBox="0 0 24 24" fill="none" stroke="#444" stroke-width="1.5"><ellipse cx="12" cy="5" rx="7" ry="3"/><path d="M5 5v14c0 1.7 3.1 3 7 3s7-1.3 7-3V5M5 12c0 1.7 3.1 3 7 3s7-1.3 7-3"/></svg></div>
  <div class="abs svc-label" style="left:100px;top:398px;text-align:right;width:195px">Data Management<br>Services</div>

  <div class="abs svc-icon" style="left:778px;top:370px"><svg width="42" height="42" viewBox="0 0 24 24" fill="none" stroke="#444" stroke-width="1.5"><rect x="4" y="3" width="16" height="18" rx="2"/><path d="M12 8l4 2v3c0 2.5-1.8 4-4 5-2.2-1-4-2.5-4-5v-3z"/></svg></div>
  <div class="abs svc-label" style="left:898px;top:398px">Ransomware<br>Protection</div>
</section>

<!-- To whom we serve -->
<h2 class="abs sec-title" style="top:1895px">TO WHOM WE SERVE</h2>
<div class="abs sec-text" style="top:1950px">The point of using Lorem Ipsum is that it has a more-or-less normal distribution of letters, as opposed to using 'Content here,<br>content here', making it look like readable English</div>

<div class="abs arrow-btn" style="left:74px;top:2078px"><svg width="12" height="12" viewBox="0 0 12 12"><path d="M8 2L4 6l4 4" fill="none" stroke="#666" stroke-width="2"/></svg></div>
<div class="abs arrow-btn" style="left:1090px;top:2078px"><svg width="12" height="12" viewBox="0 0 12 12"><path d="M4 2l4 4-4 4" fill="none" stroke="#666" stroke-width="2"/></svg></div>

<div class="abs whom-circle" style="left:143px;top:2024px"><svg width="60" height="60" viewBox="0 0 24 24" fill="none" stroke="#444" stroke-width="1"><path d="M12 3L2 21h20z"/><path d="M12 10v5M12 17v1"/></svg></div>
<div class="abs whom-label" style="left:115px;top:2200px">Risk Managers</div>

<div class="abs whom-circle" style="left:336px;top:2024px"><svg width="60" height="60" viewBox="0 0 24 24" fill="none" stroke="#444" stroke-width="1"><path d="M12 2l8 3v6c0 5-3.5 9-8 11-4.5-2-8-6-8-11V5z"/><path d="M8 12l3 3 5-6"/></svg></div>
<div class="abs whom-label" style="left:308px;top:2200px">Information<br>Security</div>

<div class="abs whom-circle active" style="left:528px;top:2024px"><svg width="60" height="60" viewBox="0 0 24 24" fill="none" stroke="#1565c0" stroke-width="1"><rect x="6" y="6" width="12" height="12"/><rect x="9" y="9" width="6" height="6"/><path d="M9 2v4M15 2v4M9 18v4M15 18v4M2 9h4M2 15h4M18 9h4M18 15h4"/></svg></div>
<div class="abs whom-label active" style="left:500px;top:2200px">Cyber Security<br>Professionals</div>

<div class="abs whom-circle" style="left:720px;top:2024px"><svg width="60" height="60" viewBox="0 0 24 24" fill="none" stroke="#444" stroke-width="1"><circle cx="12" cy="7" r="3"/><path d="M6 21v-4h12v4M4 14h16"/></svg></div>
<div class="abs whom-label" style="left:692px;top:2200px">Chief Data<br>Technicians</div>

<div class="abs whom-circle" style="left:913px;top:2024px"><svg width="60" height="60" viewBox="0 0 24 24" fill="none" stroke="#444" stroke-width="1"><circle cx="12" cy="7" r="3.5"/><path d="M5 21c0-4 3-7 7-7s7 3 7 7"/><path d="M10 14l2 3 2-3"/></svg></div>
<div class="abs whom-label" style="left:885px;top:2200px">Digital Officers</div>

<!-- Team -->
<svg class="abs team-bg" width="1200" height="720" viewBox="0 0 1200 720">
  <polygon points="0,0 200,0 0,60" fill="#8a8f96"/>
  <polygon points="0,60 200,0 1200,0 1200,720 0,720" fill="#0e57ad"/>
</svg>
<h2 class="abs sec-title team-title" style="top:2438px">OUR TEAM</h2>
<div class="abs team-sub" style="top:2490px">Our Bestest Team Members.</div>
<div class="abs arrow-btn" style="left:143px;top:2700px;width:30px;height:30px"><svg width="10" height="10" viewBox="0 0 12 12"><path d="M8 2L4 6l4 4" fill="none" stroke="#0e57ad" stroke-width="2.5"/></svg></div>
<div class="abs arrow-btn" style="left:1025px;top:2700px;width:30px;height:30px"><svg width="10" height="10" viewBox="0 0 12 12"><path d="M4 2l4 4-4 4" fill="none" stroke="#0e57ad" stroke-width="2.5"/></svg></div>

<div class="abs card" style="left:190px;top:2546px"><div class="photo" role="img" aria-label="Portrait of team member Arlo"></div><div class="name">Arlo</div><div class="role">Designation Here</div><div class="rule"></div><div class="soc"><i></i><i></i><i></i><i></i></div></div>
<div class="abs card feature" style="left:402px;top:2546px"><div class="photo" role="img" aria-label="Portrait of team member Mira Tolan"></div><div class="name">Mira Tolan</div><div class="role">Designation Here</div><div class="rule"></div><div class="soc"><i></i><i></i><i></i><i></i></div></div>
<div class="abs card" style="left:608px;top:2546px"><div class="photo" role="img" aria-label="Portrait of team member Ned Parvel"></div><div class="name">Ned Parvel</div><div class="role">Designation Here</div><div class="rule"></div><div class="soc"><i></i><i></i><i></i><i></i></div></div>
<div class="abs card" style="left:815px;top:2546px"><div class="photo" role="img" aria-label="Portrait of team member Owen Strake"></div><div class="name">Owen Strake</div><div class="role">Designation Here</div><div class="rule"></div><div class="soc"><i></i><i></i><i></i><i></i></div></div>

<!-- Blog -->
<svg class="abs" style="left:0;top:3015px" width="1200" height="645" viewBox="0 0 1200 645">
  <rect width="1200" height="645" fill="#eef4fb"/>
  <polygon points="1000,0 1200,0 1200,50" fill="#8a8f96"/>
</svg>
<h2 class="abs sec-title" style="top:3082px">LATEST BLOG POSTS</h2>
<div class="abs arrow-btn" style="left:82px;top:3330px;width:30px;height:30px"><svg width="10" height="10" viewBox="0 0 12 12"><path d="M8 2L4 6l4 4" fill="none" stroke="#666" stroke-width="2"/></svg></div>
<div class="abs arrow-btn" style="left:1088px;top:3330px;width:30px;height:30px"><svg width="10" height="10" viewBox="0 0 12 12"><path d="M4 2l4 4-4 4" fill="none" stroke="#666" stroke-width="2"/></svg></div>

<article class="abs blog-card" style="left:143px;top:3215px">
  <h3>The point of using Lorem Ipsum</h3>
  <p>"The point of using Lorem Ipsum is that it has a more-or-less normal distribution of letters, as opposed to using Content here, content here. making it look like readable English letters, as opposed to using Content here, content here."</p>
  <a>Learn More</a>
</article>
<div class="abs date" style="left:301px;top:3152px"><b>12</b><span>Feb 2019</span></div>

<article class="abs blog-card" style="left:614px;top:3215px">
  <h3>The point of using Lorem Ipsum</h3>
  <p>"The point of using Lorem Ipsum is that it has a more-or-less normal distribution of letters, as opposed to using Content here, content here. making it look like readable English letters, as opposed to using Content here, content here."</p>
  <a>Learn More</a>
</article>
<div class="abs date" style="left:772px;top:3152px"><b>06</b><span>Feb 2019</span></div>

<div class="abs btn-view">View All</div>

<!-- Get started -->
<section class="abs start" role="img" aria-label="Blue-tinted photo of a team working together in an office"></section>
<svg class="abs" style="left:0;top:3600px" width="1200" height="120" viewBox="0 0 1200 120"><polygon points="0,0 300,60 0,60" fill="#eef4fb"/><polygon points="0,60 300,60 0,100" fill="#8a8f96" opacity="0"/></svg>
<h2 class="abs sec-title start-title" style="top:3762px">LET'S GET STARTED</h2>
<div class="abs form">
  <div class="field first" style="top:0">Your Name</div>
  <div class="field" style="top:46px">Your Email</div>
  <div class="field" style="top:92px;border-bottom:none">Your Contact Number</div>
  <div class="message">Your Message</div>
</div>
<div class="abs btn-submit">Submit</div>
<div class="abs chat"><svg width="30" height="30" viewBox="0 0 24 24" fill="#1565c0"><path d="M4 4h16a2 2 0 0 1 2 2v9a2 2 0 0 1-2 2H9l-5 4v-4a2 2 0 0 1-2-2V6a2 2 0 0 1 2-2z"/></svg></div>

<!-- Footer -->
<footer class="abs footer">
  <div class="abs brand"><span class="dot"></span>Vaultmerrow</div>
  <nav class="abs menu"><span>Home</span><span>About</span><span>Services</span><span>Resources</span><span>Blog</span><span>Contact Us</span></nav>
  <div class="abs rule"></div>
  <div class="abs copy">Copyright 2019 @ Vaultmerrow. All Rights Reserved.</div>
  <div class="abs legal">Terms of services | Privacy Policy</div>
</footer>

</body>
</html>
```